Business Card for a Jewellery Brand

Business card for an upscale jewellery brand. Attached is the brand logo and icon and color board. I am looking for two card versions: one for the founder and one is generic. The card should be elegant and convey upscale and premium feel. I am open to both square and rectangle card shapes.

Industry/Entity Type

Jewelry

Contact Information for Business Card

Two cards: (1) Sunela Parvaniya (Founder) (2) General
(1) Sunela Parvaniya card should have Name: Sunela Parvaniya, Title: Founder Email id: sunela@quiremo.com.au. Phone no: +61452913307
(2) Generic card should have Email id: info@quiremo.com.au. Phone no: +61436207518

Requirements
Must have
• Workmark
• ICON
• Phone no
• Email ID
• ABN: 58219740312 (Note: ABN is Business number in Australia)
• Website: www.quiremo.com.au
• Instagram: quiremo_jewellery
• Facebook: @quiremojewellery
Nice to have
• Tagline

```html
<!DOCTYPE html>
<html lang="en">
<head>
<meta charset="utf-8">
<title>Quiremo Business Cards</title>
<link rel="stylesheet" href="https://fonts.googleapis.com/css2?family=Raleway:wght@300;400;500;600&display=swap">
<style>
  :root {
    --page: #ffffff;
    --blush: #fce8e2;
    --rose: #e3968f;
    --rose-band: rgba(225, 150, 143, 0.55);
    --stone-light: #eef0f2;
    --stone-mid: #d9dde1;
    --ink-soft: #a29d9c;
    --shadow: rgba(0, 0, 0, 0.22);
  }
  * { margin: 0; padding: 0; box-sizing: border-box; }
  html, body {
    width: 1200px;
    height: 738px;
    overflow: hidden;
    background: var(--page);
    font-family: "Raleway", sans-serif;
  }
  .canvas {
    position: relative;
    width: 1200px;
    height: 738px;
  }
  .card {
    position: absolute;
    top: 138px;
    width: 464px;
    height: 463px;
    background: var(--blush);
    box-shadow: 8px 10px 18px var(--shadow);
    overflow: hidden;
  }
  .card--social { left: 93px; }
  .card--founder { left: 643px; }

  /* Social card */
  .brand-mark {
    position: absolute;
    left: 0;
    right: 0;
    top: 92px;
    display: flex;
    flex-direction: column;
    align-items: center;
    gap: 22px;
  }
  .brand-mark__square {
    width: 62px;
    height: 62px;
    border: 6px solid var(--rose);
  }
  .brand-mark__name {
    color: var(--rose);
    font-weight: 500;
    font-size: 34px;
    letter-spacing: 10px;
    padding-left: 10px;
  }
  .accent-band {
    position: absolute;
    left: 0;
    top: 317px;
    width: 100%;
    height: 23px;
    background: var(--rose-band);
  }
  .stone-panel {
    position: absolute;
    left: 0;
    top: 340px;
    width: 100%;
    height: 123px;
    background: linear-gradient(135deg, var(--stone-light) 0%, var(--stone-mid) 55%, var(--stone-light) 100%);
  }
  .social-handle {
    position: absolute;
    left: 121px;
    display: flex;
    align-items: center;
    gap: 15px;
    color: var(--rose);
    font-weight: 400;
    font-size: 23px;
  }
  .social-handle--first { top: 359px; }
  .social-handle--second { top: 405px; }
  .social-handle__square {
    width: 30px;
    height: 30px;
    background: var(--rose);
    border-radius: 5px;
    flex: none;
  }

  /* Founder card */
  .wordmark {
    position: absolute;
    left: 0;
    right: 0;
    top: 90px;
    text-align: center;
    color: var(--rose);
    font-weight: 500;
    font-size: 52px;
    letter-spacing: 14px;
    padding-left: 14px;
  }
  .person {
    position: absolute;
    left: 0;
    right: 0;
    top: 215px;
    text-align: center;
  }
  .person__name {
    color: var(--rose);
    font-weight: 600;
    font-size: 24px;
    line-height: 30px;
  }
  .person__title {
    color: var(--ink-soft);
    font-weight: 500;
    font-size: 18px;
    line-height: 22px;
  }
  .divider {
    position: absolute;
    left: 146px;
    top: 291px;
    width: 172px;
    height: 1.5px;
    background: var(--rose);
  }
  .contact {
    position: absolute;
    left: 0;
    right: 0;
    top: 318px;
    text-align: center;
    list-style: none;
    color: var(--ink-soft);
    font-weight: 400;
    font-size: 18px;
    line-height: 25.5px;
  }
  .contact__abn { font-size: 15px; }
</style>
</head>
<body>
<main class="canvas">
  <section class="card card--social" aria-label="Social card">
    <div class="brand-mark">
      <div class="brand-mark__square"></div>
      <div class="brand-mark__name">QUIREMO</div>
    </div>
    <div class="accent-band"></div>
    <div class="stone-panel" role="img" aria-label="White marble texture with soft grey veins"></div>
    <div class="social-handle social-handle--first">
      <span class="social-handle__square"></span>
      <span>quiremo_jewellery</span>
    </div>
    <div class="social-handle social-handle--second">
      <span class="social-handle__square"></span>
      <span>@quiremojewellery</span>
    </div>
  </section>

  <section class="card card--founder" aria-label="Founder card">
    <div class="wordmark">QUIREMO</div>
    <div class="person">
      <p class="person__name">Sunela Parvaniya</p>
      <p class="person__title">Founder</p>
    </div>
    <div class="divider"></div>
    <ul class="contact">
      <li>+61452913307</li>
      <li>sunela@quiremo.com.au</li>
      <li>www.quiremo.com.au</li>
      <li class="contact__abn">ABN: 58219740312</li>
    </ul>
  </section>
</main>
</body>
</html>
```